Product label for herbal salves, lotions, soaps and tinctures

We need a very simple, clean and organic looking label that can be used for an ointment jar, a lotion bottle and a dropper bottle.
We have an existing logo (see attached). We like the colors white, olive green, gold and black. It needs to include product name as dominant and logo. It also needs to include an ingredient list, and usage statement. Include weight of product, distributed by, made in the USA, and QVX statement.
Example of what needs to be present:
Logo
Name: Tranquil Ease Blend
Used for: For Muscle Aches, Arthritis, Tendonitis, Headaches
To Use: For muscle aches, arthritis and tendonitis, massage into affected area. For tension headache apply to neck, temples and forehead.
Store in a cool and dry place, away from direct heat and sunlight.
Weight of product: 1.75
DIST. BY: Copper Brook Herbal
Made in the USA
This product is not intended to diagnose, treat, cure
or prevent any disease. Not regulated
by the QVX. Please consult your health care practitioner
before using product. Discontinue use if any adverse reaction occurs.
Ingredient list:
Wildcrafted Ingredients:
Ashwagandha Root, Peppermint Leaf, Hops Flowers, St. John’s Wort Herb, Arnica Flowers, Green Tea Leaf, Alfalfa Leaf, Dandelion Root, Burdock Root, Chickweed Herb, Chaparral Leaf, Yarrow Flowers, Boneset Herb, Moringa Leaf, Meadowsweet Herb, Nettle Leaf
Organic Ingredients:
Olive Oil, Aloe Leaf, Sweet Birch Bark, Helichrysum Flowers, Holy Basil Leaf, Borage Herb, Ginger Root, Angelica Root, White Willow Bark, Mustard Seed, Beeswax, Vitamin E, Essential Oils
Dimensions of Jar:
Circumference: 7 in.
Height: 1 in.

```html
<!DOCTYPE html>
<html lang="en">
<head>
<meta charset="utf-8">
<title>Tranquil Ease Blend – Jar Label</title>
<link rel="stylesheet" href="https://fonts.googleapis.com/css2?family=Libre+Baskerville:wght@400;700&family=Montserrat:wght@400;600&display=swap">
<style>
  :root {
    --page: #ffffff;
    --label: #ffffff;
    --olive: #66672a;
    --gold: #b98a3c;
    --gold-light: #e3c27a;
    --ink: #2b2b2b;
    --sketch: #ececec;
  }
  * { box-sizing: border-box; margin: 0; padding: 0; }
  html, body {
    width: 1200px; height: 1000px; overflow: hidden;
    background: var(--page);
  }
  .jar-label {
    position: absolute;
    left: 18px; top: 418px;
    width: 1165px; height: 165px;
    background: var(--label);
    box-shadow: 0 10px 14px rgba(0,0,0,0.28);
    font-family: "Montserrat", sans-serif;
    color: var(--ink);
    overflow: hidden;
  }
  .gold-edge {
    position: absolute; left: 0; right: 0; height: 4px;
    background: linear-gradient(90deg, var(--gold), var(--gold-light), var(--gold), var(--gold-light), var(--gold));
  }
  .gold-edge.top { top: 0; }
  .gold-edge.bottom { bottom: 0; }
  .botanical-art {
    position: absolute; top: 4px; bottom: 4px;
    background: radial-gradient(ellipse at center, var(--sketch) 0%, rgba(236,236,236,0) 70%);
  }
  .botanical-art.left { left: 120px; width: 260px; }
  .botanical-art.centre-left { left: 420px; width: 200px; }
  .botanical-art.centre-right { left: 740px; width: 220px; }
  .botanical-art.right { left: 820px; width: 320px; }

  .panel { position: absolute; font-size: 6.6px; line-height: 8.2px; }
  .panel p { margin-bottom: 0; }
  .panel .gap { margin-top: 8px; }
  .panel .heading { text-transform: uppercase; }
  .panel.ingredients { left: 30px; top: 27px; width: 285px; }
  .panel.notices { left: 940px; top: 46px; width: 215px; }

  .brand-block {
    position: absolute; left: 380px; top: 30px; width: 420px;
    text-align: center;
  }
  .brand-name {
    font-family: "Libre Baskerville", serif;
    font-weight: 700;
    font-size: 17px;
    color: var(--olive);
    display: inline-flex; align-items: center; gap: 6px;
  }
  .brand-dot {
    width: 9px; height: 9px; border-radius: 50%;
    background: var(--olive);
  }
  .brand-rule {
    width: 236px; height: 1.5px; margin: 22px auto 6px;
    background: linear-gradient(90deg, rgba(185,138,60,0), var(--gold), rgba(185,138,60,0));
  }
  .product-name {
    font-family: "Libre Baskerville", serif;
    font-weight: 400;
    font-size: 31px;
    color: var(--olive);
    letter-spacing: 0.2px;
  }
  .product-use {
    font-family: "Libre Baskerville", serif;
    font-size: 9.5px;
    color: var(--olive);
    margin-top: 6px;
    word-spacing: 1px;
  }
</style>
</head>
<body>
  <section class="jar-label">
    <div class="botanical-art left" role="img" aria-label="Fine line botanical sketch of leaves and lilies"></div>
    <div class="botanical-art centre-left" role="img" aria-label="Fine line sketch of flowering herb stems"></div>
    <div class="botanical-art centre-right" role="img" aria-label="Fine line sketch of small blossom sprigs"></div>
    <div class="botanical-art right" role="img" aria-label="Fine line botanical sketch of a rose and leaves"></div>
    <div class="gold-edge top"></div>
    <div class="gold-edge bottom"></div>

    <div class="panel ingredients">
      <p class="heading">Wildcrafted Ingredients:</p>
      <p>Ashwagandha Root, Peppermint Leaf, Hops Flowers, St. John’s Wort Herb, Arnica Flowers, Green Tea Leaf, Alfalfa Leaf, Dandelion Root, Burdock Root, Chickweed Herb, Chaparral Leaf, Yarrow Flowers, Boneset Herb, Moringa Leaf, Meadowsweet Herb, Nettle Leaf</p>
      <p class="heading">Organic Ingredients:</p>
      <p>Olive Oil, Aloe Leaf, Sweet Birch Bark, Helichrysum Flowers, Holy Basil Leaf, Borage Herb, Ginger Root, Angelica Root, White Willow Bark, Mustard Seed, Beeswax, Vitamin E, Essential Oils</p>
      <p class="heading gap">To use:</p>
      <p>For muscle aches, arthritis and tendonitis, massage into affected area. For tension headache apply to neck, temples and forehead.</p>
    </div>

    <div class="brand-block">
      <div class="brand-name"><span class="brand-dot"></span>Copper Brook Herbal</div>
      <div class="brand-rule"></div>
      <h1 class="product-name">Tranquil Ease Blend</h1>
      <p class="product-use">For Muscle Aches. Arthritis. Tendonitis. Headaches</p>
    </div>

    <div class="panel notices">
      <p class="heading">Made in the USA</p>
      <p>This product is not intended to diagnose, treat, cure or prevent any disease. Not regulated by the QVX. Please consult your health care practitioner before using product. Discontinue use if any adverse reaction occurs.</p>
      <p class="gap">Store in a cool and dry place, away from direct heat and sunlight.</p>
      <p class="gap" style="margin-top:16px">Weight of product: 1.75</p>
      <p>DIST. BY: Copper Brook Herbal</p>
    </div>
  </section>
</body>
</html>
```